German Headhunter/ HR Consultancy needs Business Cards Design

We need a business Card Design for our Company in Stuttgart. We are specialized as Headhunter/ HR Consultancy in Placement of specialist and managers in permanent employment. Please refer to our business logo.

```html
<!DOCTYPE html>
<html lang="de">
<head>
<meta charset="utf-8">
<title>Kernwerk Personalberatung – Visitenkarte</title>
<link rel="stylesheet" href="https://fonts.googleapis.com/css2?family=Montserrat:wght@600&family=Open+Sans:wght@400;600&display=swap">
<style>
  :root {
    --brand-blue: #3b57aa;
    --text-grey: #7b7b7b;
    --card-white: #ffffff;
    --stage: #e9eaee;
  }
  * { margin: 0; padding: 0; box-sizing: border-box; }
  html, body { width: 1200px; height: 1015px; overflow: hidden; }
  body {
    background: var(--stage);
    display: flex;
    flex-direction: column;
    align-items: center;
    justify-content: center;
    gap: 60px;
  }
  .card {
    width: 620px;
    height: 354px;
    position: relative;
    box-shadow: 0 6px 18px rgba(0,0,0,0.18);
  }
  .card--front {
    background: var(--brand-blue);
    display: flex;
    align-items: center;
    justify-content: center;
  }
  .card--back { background: var(--card-white); }

  .wordmark {
    display: flex;
    align-items: center;
    gap: 16px;
    font-family: "Montserrat", sans-serif;
    font-weight: 600;
    line-height: 1;
  }
  .wordmark__square { width: 44px; height: 44px; background: currentColor; }
  .wordmark__name { font-size: 40px; letter-spacing: 1px; }
  .wordmark__sub { font-size: 15px; letter-spacing: 1.5px; margin-top: 6px; }
  .card--front .wordmark { color: var(--card-white); }
  .card--back .wordmark { color: var(--brand-blue); position: absolute; left: 56px; top: 56px; }
  .card--back .wordmark__square { width: 36px; height: 36px; }
  .card--back .wordmark__name { font-size: 32px; }
  .card--back .wordmark__sub { font-size: 12px; }

  .person { position: absolute; left: 56px; top: 140px; }
  .person__name {
    font-family: "Montserrat", sans-serif; font-weight: 600;
    font-size: 20px; color: var(--brand-blue); letter-spacing: 0.5px;
  }
  .person__role {
    font-family: "Open Sans", sans-serif; font-size: 13px;
    color: var(--text-grey); letter-spacing: 1px; margin-top: 2px;
  }
  .contact {
    position: absolute; left: 56px; top: 204px;
    list-style: none; font-family: "Open Sans", sans-serif;
    font-size: 15px; color: var(--text-grey);
  }
  .contact li { display: flex; align-items: center; gap: 10px; height: 22px; }
  .contact svg { width: 14px; height: 14px; fill: var(--brand-blue); flex: none; }
  .contact .accent { color: var(--brand-blue); }
  .address {
    position: absolute; left: 56px; top: 286px;
    font-family: "Open Sans", sans-serif; font-size: 15px;
    color: var(--text-grey); line-height: 1.35;
  }
</style>
</head>
<body>
  <section class="card card--front" aria-label="Vorderseite">
    <div class="wordmark">
      <span class="wordmark__square"></span>
      <div>
        <div class="wordmark__name">KERNWERK</div>
        <div class="wordmark__sub">PERSONALBERATUNG</div>
      </div>
    </div>
  </section>

  <section class="card card--back" aria-label="Rückseite">
    <div class="wordmark">
      <span class="wordmark__square"></span>
      <div>
        <div class="wordmark__name">KERNWERK</div>
        <div class="wordmark__sub">PERSONALBERATUNG</div>
      </div>
    </div>

    <div class="person">
      <div class="person__name">LUKAS BRENNER</div>
      <div class="person__role">MANAGING DIRECTOR</div>
    </div>

    <ul class="contact">
      <li>
        <svg viewBox="0 0 24 24" aria-hidden="true"><path d="M6.6 10.8a15.1 15.1 0 0 0 6.6 6.6l2.2-2.2a1 1 0 0 1 1-.25 11.4 11.4 0 0 0 3.6.57 1 1 0 0 1 1 1V20a1 1 0 0 1-1 1A17 17 0 0 1 3 4a1 1 0 0 1 1-1h3.5a1 1 0 0 1 1 1c0 1.25.2 2.45.57 3.57a1 1 0 0 1-.25 1z"/></svg>
        0711-555 018 24
      </li>
      <li>
        <svg viewBox="0 0 24 24" aria-hidden="true"><path d="M2 5h20v14H2zm2 2v.5l8 5 8-5V7l-8 5z"/></svg>
        kontakt@kernwerk-hr.de
      </li>
      <li>
        <svg viewBox="0 0 24 24" aria-hidden="true"><path d="M12 2a10 10 0 1 0 0 20 10 10 0 0 0 0-20zm6.9 6h-2.9a15.6 15.6 0 0 0-1.4-3.6A8 8 0 0 1 18.9 8zM12 4c.8 1.2 1.5 2.5 1.9 4h-3.8c.4-1.5 1.1-2.8 1.9-4zM4.3 14a8 8 0 0 1 0-4h3.4a16.5 16.5 0 0 0 0 4zm.8 2h2.9c.3 1.3.8 2.5 1.4 3.6A8 8 0 0 1 5.1 16zM8 8H5.1a8 8 0 0 1 4.3-3.6C8.8 5.5 8.3 6.7 8 8zm4 12c-.8-1.2-1.5-2.5-1.9-4h3.8c-.4 1.5-1.1 2.8-1.9 4zm2.3-6H9.7a14.7 14.7 0 0 1 0-4h4.6a14.7 14.7 0 0 1 0 4zm.3 5.6c.6-1.1 1.1-2.3 1.4-3.6h2.9a8 8 0 0 1-4.3 3.6zm1.7-5.6a16.5 16.5 0 0 0 0-4h3.4a8 8 0 0 1 0 4z"/></svg>
        <span>www.<span class="accent">kernwerk-hr</span>.de</span>
      </li>
    </ul>

    <address class="address" style="font-style:normal">
      Talstraße 48, 70188 Stuttgart<br>Deutschland
    </address>
  </section>
</body>
</html>
```